We need a modern WIX website for Brightform Beam Services Australia (Laser/Industrial/Engineering)

We need a website for Wix (coded) for our laser restoration and industrial cleaning business.

It will need to be 4-6 pages.
Pages may include:
Home
About
Why Laser
Capabilities
There needs to be a contact / quote form

We do not want boring institutional design, so please do try to be a little creative (but not artsy, more engineering / laser etc). We hesitate with boxy wordpress looking templates, so please bring in strip backgrounds and sliders etc;

Our brand colours are blue and red, but a sharp modern site relative to the industry and work is important.

We envision the home page to take visitors on a informed journey of who, what, why, how, explaining the capability of laser science across contaminants, industries and surfaces.

We envision the home page to be strips:
- landing
- intro

-Why choose laser / What is laser cleaning
Minimum downtime, no surface damage, no environmental impact, no mess, no waste, complete restoration (we have an explainer video)

- Contaminants
Bacteria, Rust, Corrosion, Oxides, Grease, Oil, Paint, Stains, Mold, Soot / Carbon, Graffiti, Coatings, Dirt, Residue

- Surfaces
Metals, Engines/Parts/Components, Tools, Machinery, Bricks/Blockwork, Concrete, Paint, Stone, Wood, Aluminium

- Industries
Medical/Sterile, Hospitality, Bio Hazardous, Construction, Infrastructure, Property, Industrial, Engineer, Automotive, Marine, Heritage, Non Destructive Testing,

----
Here is some info on the company below:

"Background Information - Brightform Beam Services Australia (BBSA) is a leading provider of advanced laser restoration services for the residential, commercial, medical, hazardous and industrial sectors, offering waste free, chemical free and damage free complete restoration of metals, concrete, wood, stone and heritage, hygiene and hazard surfaces, with complete removal of coatings, bacteria, paint, rust, graffiti, mold and fire ash (soot), and preparation and treating for welding and bonding.
Servicing Melbourne and Victoria, with additional services available Australia wide, BBSA offers a 24/7 call-out service to your site.
With no downtime to your operations, we offer a timely resolution to your cleaning and maintenance needs."

We have attached some inspiration of websites we like the flow/feel of, but feel free to put your best designs forward.

You are welcome to use dummy headers and text at this stage, as design and feel is most important, and we can add text later.

```html
<!DOCTYPE html>
<html lang="en">
<head>
<meta charset="utf-8">
<title>Brightform Beam Services Australia</title>
<link href="https://fonts.googleapis.com/css2?family=Michroma&family=Roboto:wght@400;500;700&display=swap" rel="stylesheet">
<style>
:root{
  --ink:#0a0b10;
  --ink-2:#14161d;
  --white:#ffffff;
  --red:#e31e24;
  --blue:#1477c1;
  --muted:#c9cbd2;
  --amber:#e89a3a;
  --steel:#3a4658;
}
*{box-sizing:border-box;margin:0;padding:0}
html,body{width:1200px;height:4283px;overflow:hidden}
body{position:relative;background:var(--ink);font-family:'Roboto',sans-serif;color:var(--white)}
.abs{position:absolute}
.display{font-family:'Michroma',sans-serif;font-weight:400;letter-spacing:1px}

/* header */
.site-header{left:0;top:0;width:1200px;height:85px;background:#000;z-index:5}
.brand{left:112px;top:16px;display:flex;align-items:center;gap:10px}
.brand-mark{width:22px;height:22px;border-radius:50%;background:var(--white)}
.brand-name{font-family:'Roboto',sans-serif;font-weight:700;font-size:38px;color:var(--white);line-height:1}
.brand-sub{left:112px;top:58px;font-size:8px;color:var(--white);letter-spacing:.2px}
.nav a{position:absolute;top:34px;font-size:14px;color:var(--white);text-decoration:none}
.call-btn{left:855px;top:24px;width:234px;height:40px;background:var(--red);border-radius:3px;display:flex;align-items:center;justify-content:center;gap:8px;font-size:13px}
.call-btn b{font-weight:700}

/* hero */
.hero{left:0;top:85px;width:1200px;height:760px;background:
 radial-gradient(ellipse 260px 220px at 700px 440px,rgba(255,176,70,.75),rgba(230,120,30,.25) 55%,transparent 75%),
 radial-gradient(ellipse 420px 260px at 320px 120px,rgba(150,170,210,.55),transparent 70%),
 linear-gradient(180deg,#2a3650 0%,#1b2540 45%,#0f1424 75%,var(--ink) 100%)}
.hero-card{left:89px;top:290px;width:427px;height:276px;background:rgba(40,40,44,.88)}
.tag{left:112px;top:313px;width:191px;height:37px;background:var(--blue);font-size:14px;font-weight:700;letter-spacing:4px;display:flex;align-items:center;justify-content:center}
.hero-title{left:112px;top:362px;font-size:48px}
.hero-text{left:112px;top:425px;width:390px;font-size:20px;line-height:26px}
.btn-red{background:var(--red);color:var(--white);font-weight:700;font-size:13px;display:flex;align-items:center;justify-content:center;border-radius:2px}
.hero-btn{left:112px;top:497px;width:131px;height:40px}
.scroll-dot{width:37px;height:37px;border-radius:50%;background:var(--white);display:flex;align-items:center;justify-content:center}

/* about */
.about-photo{left:120px;top:875px;width:420px;height:420px;background:linear-gradient(180deg,#6f7f99 0%,#3d4e6b 45%,#1a2646 75%,#0c1330 100%)}
.frame-red{left:112px;top:862px;width:160px;height:176px;border-top:3px solid var(--red);border-left:3px solid var(--red)}
.frame-white{left:398px;top:1132px;width:160px;height:178px;border-bottom:6px solid var(--white);border-right:6px solid var(--white)}
.about-title{left:612px;top:866px;font-size:50px}
.about-copy{left:612px;top:946px;width:474px;font-size:13.6px;line-height:25.8px;text-align:justify;color:#e8e9ee}
.about-copy p+p{margin-top:26px}
.about-btn{left:612px;top:1280px;width:130px;height:38px}

/* why */
.why{left:0;top:1415px;width:1200px;height:600px;background:
 radial-gradient(ellipse 500px 200px at 600px 470px,rgba(90,70,50,.45),transparent 70%),
 linear-gradient(180deg,var(--ink) 0%,#1c222d 30%,#232a36 60%,var(--ink) 100%)}
.why-title{left:0;top:1548px;width:1200px;text-align:center;font-size:50px}
.feature{background:var(--white);color:#111;display:flex;flex-direction:column;align-items:center;justify-content:flex-start;padding-top:26px;text-align:center;font-weight:500;font-size:16px;line-height:26px}
.feature svg{margin-bottom:10px}
.feature.active{background:var(--blue);color:var(--white);padding-top:40px}

/* video */
.video{left:111px;top:2056px;width:978px;height:484px;background:
 radial-gradient(ellipse 300px 180px at 500px 260px,rgba(240,150,50,.7),rgba(160,80,30,.3) 55%,transparent 80%),
 linear-gradient(160deg,#4a4a4e 0%,#2a2b30 50%,#141418 100%)}
.play{left:562px;top:2261px;width:72px;height:72px;border-radius:50%;background:var(--red);display:flex;align-items:center;justify-content:center}

/* tabs */
.tabs{left:0;top:2657px;width:1200px;height:130px;display:flex}
.tab{flex:1;display:flex;align-items:center;justify-content:center;font-size:29px;font-weight:700;background:var(--white);color:#111}
.tab.active{background:var(--red);color:var(--white)}
.tab-pointer{left:582px;top:2786px}
.surface{width:140px;text-align:center;font-size:16px;font-weight:700}
.surface .disc{width:108px;height:108px;border-radius:50%;background:#1f2127;margin:0 auto 18px;display:flex;align-items:center;justify-content:center}

/* contact */
.contact{left:111px;top:3317px;width:978px;height:551px;background:var(--blue)}
.contact-title{left:0;top:3380px;width:1200px;text-align:center;font-size:48px}
.field{border:2px solid rgba(255,255,255,.85);font-size:13px;color:var(--white);padding-left:22px;display:flex;align-items:center}
.field.msg{align-items:flex-start;padding-top:22px}
.submit{left:460px;top:3711px;width:280px;height:64px}

/* footer */
.footer{left:0;top:3890px;width:1200px;height:393px;background:linear-gradient(180deg,var(--ink) 0%,#0e1118 60%,#1a1d24 100%)}
.foot-h{top:3970px;font-size:21px;font-weight:700}
.foot-list{top:4010px;list-style:none;font-size:14px;line-height:26px}
.foot-list li::before{content:"»";margin-right:14px}
.foot-list.support li::before{content:none}
.foot-list.support li{display:flex;align-items:center;gap:12px}
.social{top:4009px;left:950px;display:flex;gap:7px}
.social span{width:33px;height:34px;border:2px solid #fff;background:#111}
.copyright{left:0;top:4184px;width:1200px;text-align:center;font-size:13px}
</style>
</head>
<body>

<header class="abs site-header">
  <div class="abs brand"><span class="brand-mark"></span><span class="brand-name">BBSA</span></div>
  <div class="abs brand-sub">BRIGHTFORM BEAM SERVICES AUSTRALIA</div>
  <nav class="nav">
    <a style="left:406px">Home</a>
    <a style="left:482px">About</a>
    <a style="left:556px">Why Laser</a>
    <a style="left:660px">Capabilities</a>
    <a style="left:771px">Contact</a>
  </nav>
  <div class="abs call-btn">
    <svg width="13" height="13" viewBox="0 0 24 24"><path fill="#fff" d="M6.6 10.8a15 15 0 0 0 6.6 6.6l2.2-2.2a1 1 0 0 1 1-.25 11.4 11.4 0 0 0 3.6.57 1 1 0 0 1 1 1V20a1 1 0 0 1-1 1A17 17 0 0 1 3 4a1 1 0 0 1 1-1h3.5a1 1 0 0 1 1 1c0 1.25.2 2.45.57 3.57a1 1 0 0 1-.25 1z"/></svg>
    <span>Call Us : <b>+61 3 9000 4417</b></span>
  </div>
</header>

<section class="abs hero" role="img" aria-label="Close-up photo of a laser cutting head throwing bright orange sparks against a blue industrial backdrop"></section>
<div class="abs hero-card"></div>
<div class="abs tag">WELCOME TO</div>
<h1 class="abs hero-title display">BBSA</h1>
<p class="abs hero-text">We are a laser restoration and industrial cleaning business</p>
<div class="abs btn-red hero-btn">GET STARTED</div>
<div class="abs scroll-dot" style="left:1126px;top:390px"><svg width="14" height="14" viewBox="0 0 24 24"><path d="M5 15l7-7 7 7" fill="none" stroke="#111" stroke-width="2.5"/></svg></div>
<div class="abs scroll-dot" style="left:1126px;top:442px"><svg width="14" height="14" viewBox="0 0 24 24"><path d="M5 9l7 7 7-7" fill="none" stroke="#111" stroke-width="2.5"/></svg></div>

<div class="abs frame-red"></div>
<div class="abs about-photo" role="img" aria-label="Photo of an industrial laser machine head firing a fine beam onto a work bed"></div>
<div class="abs frame-white"></div>
<h2 class="abs about-title display">ABOUT US</h2>
<div class="abs about-copy">
  <p>Brightform Beam Services Australia (BBSA) is a leading provider of advanced laser restoration services for the residential, commercial, medical, hazardous and industrial sectors, offering waste free, chemical free and damage free complete restoration of metals, concrete, wood, stone and heritage, hygiene and hazard surfaces, with complete removal of coatings, bacteria, paint, rust, graffiti, mold and fire ash (soot), and preparation and treating for welding and bonding.</p>
  <p>Servicing Melbourne and Victoria, with additional services available Australia wide, BBSA offers a 24/7 call-out service to your site. With no downtime to your operations, we offer a timely resolution to your cleaning and maintenance needs.</p>
</div>
<div class="abs btn-red about-btn">READ MORE</div>

<section class="abs why" role="img" aria-label="Dark background photo of a perforated metal sheet under a laser with faint sparks"></section>
<h2 class="abs why-title display">WHY CHOOSE LASER</h2>

<div class="abs feature" style="left:111px;top:1660px;width:172px;height:188px">
  <svg width="70" height="70" viewBox="0 0 70 70" fill="#1477c1"><circle cx="35" cy="35" r="10"/><path d="M6 6l16 16M22 10v12H10M64 6L48 22M48 10v12h12M6 64l16-16M10 48h12v12M64 64L48 48M60 48H48v12" stroke="#1477c1" stroke-width="5" fill="none"/></svg>
  <span>Minimum<br>Downtime</span>
</div>
<div class="abs feature active" style="left:284px;top:1634px;width:237px;height:241px">
  <svg width="70" height="70" viewBox="0 0 70 70" fill="none" stroke="#fff" stroke-width="5"><path d="M20 30l15-8 15 8v18l-15 8-15-8z"/><path d="M35 22V6M28 12l7-7 7 7M10 56l-6-6 6-6M60 56l6-6-6-6"/></svg>
  <span>No surface<br>Damage</span>
</div>
<div class="abs feature" style="left:522px;top:1660px;width:171px;height:188px">
  <svg width="70" height="70" viewBox="0 0 70 70" fill="#1477c1"><path d="M4 44h14l14 6h14l12-8 6 4-18 14H18l-14-4z"/><path d="M36 40V18" stroke="#1477c1" stroke-width="4"/><path d="M36 22c0-10 8-16 18-16 0 10-8 16-18 16zM36 26c0-8-6-12-14-12 0 8 6 12 14 12z"/></svg>
  <span>No Environmental<br>Impact</span>
</div>
<div class="abs feature" style="left:705px;top:1660px;width:185px;height:188px">
  <svg width="70" height="70" viewBox="0 0 70 70" fill="none" stroke="#1477c1" stroke-width="4"><path d="M10 6v58M24 6v58M38 6v58M52 6v58M4 22h62M4 46h62M66 10v50"/></svg>
  <span>No Mess</span>
</div>
<div class="abs feature" style="left:902px;top:1660px;width:187px;height:188px">
  <svg width="70" height="70" viewBox="0 0 70 70" fill="#1477c1"><rect x="12" y="12" width="46" height="7"/><rect x="28" y="5" width="14" height="7"/><path d="M16 22h38l-4 42H20z"/><path d="M28 30v26M35 30v26M42 30v26" stroke="#fff" stroke-width="3"/></svg>
  <span>No Waste</span>
</div>

<div class="abs video" role="img" aria-label="Explainer video still: laser head cutting a perforated steel sheet with a shower of sparks"></div>
<div class="abs play"><svg width="22" height="24" viewBox="0 0 22 24"><path d="M4 2l16 10L4 22z" fill="#fff"/></svg></div>

<div class="abs tabs">
  <div class="tab">CONTAMINANTS</div>
  <div class="tab active">SURFACES</div>
  <div class="tab">INDUSTRIES</div>
</div>
<svg class="abs tab-pointer" width="36" height="34" viewBox="0 0 36 34"><path d="M0 0h36L18 34z" fill="#e31e24"/></svg>

<div class="abs surface" style="left:138px;top:2871px"><div class="disc"><svg width="48" height="48" viewBox="0 0 48 48" fill="#fff"><path d="M6 30l18-8 18 4-18 10z"/><path d="M6 20l18-8 18 4-18 10z" opacity=".8"/></svg></div>Metals</div>
<div class="abs surface" style="left:334px;top:2871px"><div class="disc"><svg width="50" height="40" viewBox="0 0 50 40" fill="#fff"><rect x="10" y="10" width="28" height="22"/><rect x="16" y="4" width="16" height="6"/><rect x="2" y="16" width="8" height="10"/><rect x="38" y="14" width="10" height="14"/></svg></div>Engines</div>
<div class="abs surface" style="left:530px;top:2871px"><div class="disc"><svg width="46" height="46" viewBox="0 0 46 46" fill="#fff"><circle cx="23" cy="23" r="16"/><circle cx="23" cy="23" r="6" fill="#1f2127"/><path d="M6 40l12-12" stroke="#fff" stroke-width="6"/></svg></div>Tools</div>
<div class="abs surface" style="left:724px;top:2871px"><div class="disc"><svg width="44" height="48" viewBox="0 0 44 48" fill="#fff"><rect x="6" y="4" width="20" height="16"/><rect x="4" y="26" width="36" height="16" rx="8"/><circle cx="14" cy="34" r="4" fill="#1f2127"/><circle cx="30" cy="34" r="4" fill="#1f2127"/></svg></div>Machinery</div>
<div class="abs surface" style="left:920px;top:2871px"><div class="disc"><svg width="50" height="44" viewBox="0 0 50 44" fill="#fff"><rect x="14" y="2" width="22" height="10"/><rect x="4" y="16" width="20" height="10"/><rect x="26" y="16" width="20" height="10"/><rect x="2" y="30" width="22" height="10"/><rect x="26" y="30" width="22" height="10"/></svg></div>Bricks</div>

<div class="abs surface" style="left:138px;top:3059px"><div class="disc"><svg width="52" height="40" viewBox="0 0 52 40" fill="#fff"><path d="M4 8h26l6 10v12H4z"/><rect x="36" y="16" width="14" height="14"/><circle cx="12" cy="34" r="5"/><circle cx="40" cy="34" r="5"/></svg></div>Concrete</div>
<div class="abs surface" style="left:334px;top:3059px"><div class="disc"><svg width="48" height="48" viewBox="0 0 48 48"><path d="M24 4a20 20 0 1 0 0 40c4 0 4-6 0-8s0-8 6-8h8c4 0 6-4 6-8A20 20 0 0 0 24 4z" fill="#fff"/><circle cx="14" cy="20" r="3.5" fill="#1f2127"/><circle cx="22" cy="12" r="3.5" fill="#1f2127"/><circle cx="14" cy="30" r="3.5" fill="#1f2127"/></svg></div>Paint</div>
<div class="abs surface" style="left:530px;top:3059px"><div class="disc"><svg width="46" height="46" viewBox="0 0 46 46" fill="none" stroke="#fff" stroke-width="3"><rect x="3" y="3" width="40" height="40"/><path d="M3 18l14-4 8 10 18-6M17 14l-2 29M25 24l6 19"/></svg></div>Stone</div>
<div class="abs surface" style="left:724px;top:3059px"><div class="disc"><svg width="52" height="40" viewBox="0 0 52 40" fill="#fff"><rect x="14" y="4" width="34" height="32" rx="4"/><circle cx="12" cy="26" r="10"/><circle cx="12" cy="26" r="4" fill="#1f2127"/></svg></div>Wood</div>
<div class="abs surface" style="left:920px;top:3059px"><div class="disc"><svg width="42" height="48" viewBox="0 0 42 48" fill="none" stroke="#fff" stroke-width="3"><rect x="4" y="4" width="34" height="40"/><path d="M14 10v28M24 14l-8 22M32 10v28"/></svg></div>Aluminium</div>

<section class="abs contact"></section>
<h2 class="abs contact-title display">CONTACT US</h2>
<div class="abs field" style="left:161px;top:3473px;width:280px;height:63px">Name</div>
<div class="abs field" style="left:460px;top:3473px;width:280px;height:63px">Email</div>
<div class="abs field" style="left:759px;top:3473px;width:280px;height:63px">Phone</div>
<div class="abs field msg" style="left:161px;top:3557px;width:878px;height:130px">Message</div>
<div class="abs btn-red submit">SUBMIT NOW</div>

<footer class="abs footer"></footer>
<h3 class="abs foot-h" style="left:111px">LINKS</h3>
<ul class="abs foot-list" style="left:111px"><li>Home</li><li>About</li><li>Testimonials</li><li>Contact</li></ul>
<h3 class="abs foot-h" style="left:354px">INFORMATION</h3>
<ul class="abs foot-list" style="left:354px"><li>About</li><li>Services</li><li>Privacy Policy</li><li>Terms of Condition</li></ul>
<h3 class="abs foot-h" style="left:650px">SUPPORT</h3>
<ul class="abs foot-list support" style="left:650px">
  <li><svg width="12" height="14" viewBox="0 0 24 28"><path d="M12 0a10 10 0 0 0-10 10c0 8 10 18 10 18s10-10 10-18A10 10 0 0 0 12 0z" fill="#fff"/><circle cx="12" cy="10" r="4" fill="#111"/></svg>Lorem ipsum dolor sit amet</li>
  <li><svg width="12" height="12" viewBox="0 0 24 24"><path fill="#fff" d="M6.6 10.8a15 15 0 0 0 6.6 6.6l2.2-2.2a1 1 0 0 1 1-.25 11.4 11.4 0 0 0 3.6.57 1 1 0 0 1 1 1V20a1 1 0 0 1-1 1A17 17 0 0 1 3 4a1 1 0 0 1 1-1h3.5a1 1 0 0 1 1 1c0 1.25.2 2.45.57 3.57a1 1 0 0 1-.25 1z"/></svg>+61 3 9000 4417</li>
  <li><svg width="13" height="10" viewBox="0 0 26 20"><rect width="26" height="20" rx="2" fill="#fff"/><path d="M1 2l12 9 12-9" stroke="#111" stroke-width="2" fill="none"/></svg>hello@brightformbeam.au</li>
</ul>
<h3 class="abs foot-h" style="left:947px">FOLLOW US</h3>
<div class="abs social"><span></span><span></span><span></span><span></span></div>
<p class="abs copyright">© Copyrights Brightform Beam Services 2023. All rights reserved</p>

</body>
</html>
```